Board to put on a meditation centre - Lantern Grove

I need a board design for a new meditation centre based in Oslo which offers free courses in meditation and self-empowerment. The size of the board is width 374cm x height 104cm.  The name of the meditation centre together with subtitles should be on the board but also some elegant decoration that matches the theme (lantern grove/meditation).
Here is the website of the meditation centre to give you a feeling of it: https://kvitfjellsenteret.no/
Good if you can use a blue color close to this one: rgb(37, 180, 193) as well as some brown/golden color (similar to the palette on the website).
On the board it should say:
Kveldens lund (in big letters, the rest is subtitles)
Meditasjon & Spirituell visdom
Kurs - Retreat - Dialog
kveldslund-senter.no
The design should be very elegant and beautiful and the feeling should be of "A Lantern Grove". A logo is here attached and should be used but I need to get a better quality version of it, will upload that as soon as possible.

```html
<!DOCTYPE html>
<html lang="no">
<head>
<meta charset="utf-8">
<title>Kveldens lund – skilt</title>
<link href="https://fonts.googleapis.com/css2?family=Bebas+Neue&family=Montserrat:wght@500;600;700&display=swap" rel="stylesheet">
<style>
  :root {
    --teal: #25b4c1;
    --teal-pale: #bfe6ea;
    --ink: #2b2b2b;
    --sand: #c1b5a5;
    --sand-soft: #e9e4dd;
    --paper: #ffffff;
    --page: #ffffff;
  }
  html, body {
    margin: 0;
    width: 1110px;
    height: 1200px;
    overflow: hidden;
    background: var(--page);
  }
  .board {
    position: absolute;
    left: 30px;
    top: 454px;
    width: 1050px;
    height: 292px;
    background: var(--paper);
    overflow: hidden;
    box-shadow: 0 12px 40px rgba(0,0,0,0.16);
    font-family: "Montserrat", sans-serif;
  }
  .board-shapes {
    position: absolute;
    inset: 0;
  }
  .title {
    position: absolute;
    left: 60px;
    top: 36px;
    margin: 0;
    font-family: "Bebas Neue", sans-serif;
    font-weight: 400;
    font-size: 110px;
    line-height: 1;
    letter-spacing: 3px;
    white-space: nowrap;
  }
  .title-first { color: var(--teal); }
  .title-second { color: var(--ink); }
  .subtitle {
    position: absolute;
    left: 61px;
    top: 131px;
    margin: 0;
    font-weight: 700;
    font-size: 27px;
    letter-spacing: 2px;
    color: var(--ink);
    white-space: nowrap;
  }
  .offers {
    position: absolute;
    left: 63px;
    top: 169px;
    display: flex;
    gap: 40px;
    margin: 0;
    padding: 0;
    list-style: none;
  }
  .offer {
    display: flex;
    align-items: center;
    gap: 8px;
    font-weight: 600;
    font-size: 30px;
    color: var(--ink);
  }
  .offer svg { width: 30px; height: 30px; }
  .footer {
    position: absolute;
    left: 61px;
    top: 230px;
    display: flex;
    align-items: center;
    gap: 10px;
  }
  .org {
    display: flex;
    align-items: center;
    gap: 6px;
    font-weight: 500;
    font-size: 11px;
    letter-spacing: 1.5px;
    text-transform: uppercase;
    color: #8a7f74;
  }
  .org-mark {
    width: 22px;
    height: 22px;
    border-radius: 50%;
    background: #d23c52;
  }
  .site {
    display: flex;
    align-items: center;
    gap: 6px;
    font-weight: 500;
    font-size: 17px;
    color: var(--ink);
  }
  .site svg { width: 18px; height: 18px; }
</style>
</head>
<body>
  <main class="board">
    <svg class="board-shapes" viewBox="0 0 1050 292" width="1050" height="292">
      <defs>
        <radialGradient id="glow" cx="848" cy="161" r="330" gradientUnits="userSpaceOnUse">
          <stop offset="0.45" stop-color="#f2f2f2"/>
          <stop offset="1" stop-color="#ffffff"/>
        </radialGradient>
        <linearGradient id="glowFade" x1="0" x2="1" y1="0" y2="0">
          <stop offset="0" stop-color="#fff" stop-opacity="1"/>
          <stop offset="0.25" stop-color="#fff" stop-opacity="0"/>
        </linearGradient>
      </defs>
      <rect x="620" y="0" width="430" height="292" fill="url(#glow)"/>
      <rect x="620" y="0" width="430" height="292" fill="url(#glowFade)"/>
      <circle cx="-6" cy="228" r="46" fill="none" stroke="var(--sand-soft)" stroke-width="5"/>
      <circle cx="-6" cy="228" r="37" fill="var(--teal-pale)"/>
      <circle cx="494" cy="300" r="55" fill="none" stroke="var(--sand-soft)" stroke-width="6"/>
      <circle cx="494" cy="300" r="45" fill="var(--teal-pale)"/>
      <g fill="none" stroke="var(--sand)" stroke-width="0.8">
        <circle cx="566" cy="222" r="1.4"/><circle cx="574" cy="222" r="1.4"/><circle cx="582" cy="222" r="1.4"/><circle cx="590" cy="222" r="1.4"/><circle cx="598" cy="222" r="1.4"/><circle cx="606" cy="222" r="1.4"/><circle cx="614" cy="222" r="1.4"/>
        <circle cx="566" cy="229" r="1.4"/><circle cx="574" cy="229" r="1.4"/><circle cx="582" cy="229" r="1.4"/><circle cx="590" cy="229" r="1.4"/><circle cx="598" cy="229" r="1.4"/><circle cx="606" cy="229" r="1.4"/><circle cx="614" cy="229" r="1.4"/>
        <circle cx="566" cy="236" r="1.4"/><circle cx="574" cy="236" r="1.4"/><circle cx="582" cy="236" r="1.4"/><circle cx="590" cy="236" r="1.4"/><circle cx="598" cy="236" r="1.4"/><circle cx="606" cy="236" r="1.4"/><circle cx="614" cy="236" r="1.4"/>
        <circle cx="566" cy="243" r="1.4"/><circle cx="574" cy="243" r="1.4"/><circle cx="582" cy="243" r="1.4"/><circle cx="590" cy="243" r="1.4"/><circle cx="598" cy="243" r="1.4"/><circle cx="606" cy="243" r="1.4"/><circle cx="614" cy="243" r="1.4"/>
        <circle cx="566" cy="250" r="1.4"/><circle cx="574" cy="250" r="1.4"/><circle cx="582" cy="250" r="1.4"/><circle cx="590" cy="250" r="1.4"/><circle cx="598" cy="250" r="1.4"/><circle cx="606" cy="250" r="1.4"/><circle cx="614" cy="250" r="1.4"/>
      </g>
      <circle cx="848" cy="165" r="176" fill="#fff" stroke="var(--sand)" stroke-width="5"/>
      <circle cx="848" cy="165" r="156" fill="var(--teal)" role="img" aria-label="Person som mediterer i lotusstilling foran et mandalamønster"/>
    </svg>

    <h1 class="title"><span class="title-first">KVELDENS</span> <span class="title-second">LUND</span></h1>
    <p class="subtitle">MEDITASJON &amp; SPIRITUELL VISDOM</p>

    <ul class="offers">
      <li class="offer">
        <svg viewBox="0 0 30 30" aria-hidden="true">
          <rect x="4" y="9" width="22" height="15" rx="2" fill="var(--teal)"/>
          <path d="M8 5 L15 2 L22 5 L15 8 Z" fill="var(--sand)"/>
          <rect x="8" y="14" width="14" height="2" fill="#fff"/>
          <rect x="8" y="18" width="9" height="2" fill="#fff"/>
        </svg>Kurs
      </li>
      <li class="offer">
        <svg viewBox="0 0 30 30" aria-hidden="true">
          <ellipse cx="15" cy="14" rx="5" ry="10" fill="var(--sand)"/>
          <path d="M3 12 Q5 24 15 25 Q9 20 8 14 Z" fill="var(--teal)"/>
          <path d="M27 12 Q25 24 15 25 Q21 20 22 14 Z" fill="var(--teal)"/>
        </svg>Retreat
      </li>
      <li class="offer">
        <svg viewBox="0 0 30 30" aria-hidden="true">
          <path d="M3 3 H20 V17 H9 L5 21 V17 H3 Z" fill="var(--sand)"/>
          <path d="M22 9 H27 V23 H25 V27 L21 23 H12 V19 H22 Z" fill="var(--teal)"/>
          <rect x="6" y="7" width="11" height="2" fill="#fff"/>
          <rect x="6" y="11" width="8" height="2" fill="#fff"/>
        </svg>Dialog
      </li>
    </ul>

    <div class="footer">
      <div class="org"><span class="org-mark"></span>Stillhavn Senter</div>
      <div class="site">
        <svg viewBox="0 0 18 18" aria-hidden="true">
          <circle cx="9" cy="9" r="8" fill="var(--teal)"/>
          <circle cx="9" cy="9" r="4.5" fill="none" stroke="#fff" stroke-width="1.4"/>
          <line x1="4.5" y1="9" x2="13.5" y2="9" stroke="#fff" stroke-width="1.2"/>
        </svg>
        kveldslund-senter.no
      </div>
    </div>
  </main>
</body>
</html>
```